Northfield Builders Guild Business card

We are looking for a new business card design with photo included.
Our business is a nonprofit construction contractor membership organization. We offer business education, assist with business setup and licensing, provide safety training, and provide a member directory.
URL: www.builderslinkguild.org
Color code:
CMYK: 0 cyan, 42 magenta, 100 yellow, 0 black for Print.
Hexidecimal: #FF9900
RGB: R 255; G 153; B 0

```html
<!DOCTYPE html>
<html lang="en">
<head>
<meta charset="utf-8">
<title>Northfield Builders Guild – Business Card</title>
<link rel="stylesheet" href="https://fonts.googleapis.com/css2?family=Montserrat:wght@400;500;600;800&display=swap">
<style>
  :root {
    --orange: #F7941D;
    --brand-orange: #FF9900;
    --charcoal: #333333;
    --ink: #3a3a3a;
    --rule: #8a8a8a;
    --paper: #ffffff;
    --backdrop: #e4e4e4;
  }
  * { box-sizing: border-box; margin: 0; padding: 0; }
  html, body {
    width: 1200px; height: 1200px; overflow: hidden;
    background: var(--backdrop);
    font-family: "Montserrat", sans-serif;
  }
  .canvas { position: relative; width: 1200px; height: 1200px; }
  .card {
    position: absolute; left: 257px; width: 686px; height: 392px;
    border-radius: 18px; overflow: hidden;
  }
  .card-front { top: 165px; background: var(--paper); }
  .card-back { top: 653px; background: var(--orange); }

  .wordmark {
    position: absolute; right: 46px; top: 46px; text-align: right;
    font-weight: 800; color: var(--charcoal);
    font-size: 30px; line-height: 1.05; letter-spacing: -0.5px;
    text-transform: uppercase;
  }
  .person { position: absolute; left: 45px; top: 206px; }
  .person-name {
    font-weight: 600; font-size: 22px; color: var(--ink); letter-spacing: 0.3px;
  }
  .person-title { font-size: 16px; color: var(--orange); margin-top: 1px; }
  .divider {
    position: absolute; left: 45px; right: 45px; top: 263px;
    height: 1.5px; background: var(--rule);
  }
  .contacts {
    position: absolute; left: 45px; top: 276px; list-style: none;
    font-size: 15.5px; color: var(--ink);
  }
  .contacts li { display: flex; align-items: center; height: 19.5px; }
  .contacts svg { width: 12px; height: 12px; margin-right: 11px; fill: var(--orange); }
  .address {
    position: absolute; right: 45px; top: 274px; text-align: right;
    font-size: 15.5px; line-height: 19.5px; color: var(--ink); font-style: normal;
  }
  .band { position: absolute; bottom: 0; height: 15px; }
  .band-orange { left: 0; width: 342px; background: var(--orange); }
  .band-dark { left: 342px; right: 0; background: var(--charcoal); }

  .back-mark {
    position: absolute; left: 0; right: 0; top: 128px; text-align: center;
    font-weight: 800; font-size: 46px; line-height: 1.05; letter-spacing: -0.5px;
    color: var(--charcoal); text-transform: uppercase;
  }
  .back-url {
    position: absolute; left: 0; right: 0; top: 323px; text-align: center;
    font-size: 15px; letter-spacing: 3px; color: var(--paper);
  }
</style>
</head>
<body>
<main class="canvas">
  <section class="card card-front" aria-label="Business card front">
    <div class="wordmark">Northfield<br>Builders Guild</div>

    <div class="person">
      <div class="person-name">DANIEL CARTER</div>
      <div class="person-title">President</div>
    </div>
    <div class="divider"></div>

    <ul class="contacts">
      <li><svg viewBox="0 0 12 12"><path d="M2.3 0.8l2 2.1-1 1.3c.7 1.6 1.9 2.8 3.5 3.5l1.3-1 2.1 2-1.2 1.8C5.2 10.4 1.6 6.8 0.5 2z"/></svg>(555) 201-4830</li>
      <li><svg viewBox="0 0 12 12"><path d="M3 0h6v12H3zM4 1.5v8h4v-8zM5.4 10.3h1.2v.9H5.4z" fill-rule="evenodd"/></svg>555.318.0247</li>
      <li><svg viewBox="0 0 12 12"><path d="M0 2.5h12v7H0zM1 3.3l5 3.4 5-3.4"/></svg>support@nbguild.org</li>
      <li><svg viewBox="0 0 12 12"><circle cx="6" cy="6" r="5.5"/></svg>builderslinkguild.org</li>
    </ul>

    <address class="address">
      2400 Harbor Mill Rd<br>
      Suite #210<br>
      Riverton, OR 97000
    </address>

    <div class="band band-orange"></div>
    <div class="band band-dark"></div>
  </section>

  <section class="card card-back" aria-label="Business card back">
    <div class="back-mark">Northfield<br>Builders Guild</div>
    <div class="back-url">www.builderslinkguild.org</div>
  </section>
</main>
</body>
</html>
```